Need a website to promote and sell my book

Using images from the book, I need a website designed that helps promote the book and eventually sell it.
*Need a landing page
*About the author page
*Storefront page to purchase
*Coming soon page
*"Featured in" page that can link to news articles etc.
The images posted here are examples, the winner of the contest will get the images from the finished book. I will provide the exact text to the winner of the contest.

I can also provide images of kids reading the book. For now, I'll just use one, the winner can have them all to choose from.
Updates

Extending deadline to allow for a few more designers to submit and to allow time for me to review and hold a poll

Target Market(s)

Parents, aunts, uncles, grandparents, friends who have kids; teachers, daycare teachers, babysitters etc.

Industry/Entity Type

Custom Publishing

Coding

Coded - Design and coding required

Number of Pages Required

5+ page

Font styles to use
Sans Serif

Colors

Designer to choose colors to be used in the design.

Requirements
Must have
• It must have a fun feel like the book.
Nice to have
• Would be great to have a section that automatically pulls tweets about the book into it.

```html
<!DOCTYPE html>
<html lang="en">
<head>
<meta charset="utf-8">
<title>Storefront – Margot</title>
<link href="https://fonts.googleapis.com/css2?family=Libre+Baskerville:ital,wght@0,400;0,700;1,400&family=Montserrat:wght@700&display=swap" rel="stylesheet">
<style>
:root{
  --ink:#2b2a28;
  --muted:#8c8a86;
  --accent:#e0533c;
  --sand:#f3f1ec;
  --line:#d9d6d0;
  --white:#ffffff;
}
*{margin:0;padding:0;box-sizing:border-box}
html,body{width:758px;height:1200px;overflow:hidden;background:var(--white)}
body{position:relative;font-family:"Libre Baskerville",Georgia,serif;color:var(--ink)}
.abs{position:absolute}

/* header */
.nav a{position:absolute;top:36px;font-size:7.5px;letter-spacing:.6px;color:var(--ink);text-decoration:none;text-transform:uppercase}
.nav a.active{color:var(--accent);text-decoration:underline}
.brand{position:absolute;left:300px;top:24px;width:116px;text-align:center}
.brand-name{font-size:15px;letter-spacing:3px;border-bottom:1px solid var(--line);padding-bottom:2px}
.brand-tag{font-size:5px;letter-spacing:.8px;margin-top:4px;color:var(--ink)}

/* page banner */
.banner{left:0;top:82px;width:758px;height:143px;background:linear-gradient(90deg,#ebe8e2 0%,#e4e0d9 45%,#dedad2 75%,#e6e2db 100%)}
.banner-title{left:102px;top:140px;font-size:21px;letter-spacing:.8px;font-weight:400}
.crumbs{right:101px;top:148px;font-size:10px;font-style:italic}
.crumbs span{color:var(--accent)}

/* product */
.product-art{left:100px;top:306px;width:258px;height:226px;background:linear-gradient(120deg,#8cc6e6,#5fa9d6 55%,#f1d9a7);border-radius:3px}
.price{left:383px;top:272px;font-size:8.5px}
.price s{color:var(--muted);font-size:7px;margin-right:6px}
.price b{color:var(--accent);font-weight:400}
.product-title{left:383px;top:296px;font-size:15.5px;font-weight:400}
.rating{left:383px;top:328px;display:flex;align-items:center;gap:3px}
.rating em{font-size:6px;color:var(--accent);margin-left:6px}
.summary{left:383px;top:347px;width:272px;font-size:7px;line-height:14.5px}
.qty-label{left:383px;top:411px;font-size:8px;letter-spacing:.3px}
.qty{left:445px;top:406px;width:57px;height:19px;background:#eeeeee;display:flex;justify-content:space-around;align-items:center;font-size:7.5px}
.qty .step{color:var(--muted)}
.cart-btn{left:383px;top:444px;width:82px;height:28px;background:var(--accent);color:var(--white);font-family:Montserrat,Arial,sans-serif;font-size:6.5px;font-weight:700;display:flex;align-items:center;justify-content:center;gap:4px;border-radius:1px}
.rule{left:385px;top:492px;width:272px;height:1px;background:var(--line)}
.meta{left:385px;font-size:8px;color:var(--muted)}
.meta i{font-size:6.5px;color:var(--ink);margin-left:3px}

/* tabs */
.tabs-area{left:0;top:590px;width:758px;height:323px;background:var(--sand)}
.tab{top:633px;font-size:19.5px;white-space:nowrap}
.tab.inactive{color:#a8a6a2}
.tab-line{left:0;top:663px;width:758px;height:1px;background:var(--line)}
.tab-underline{left:223px;top:662px;width:111px;height:2px;background:var(--accent)}
.description{left:148px;top:696px;width:462px;text-align:center;font-size:8.5px;font-style:italic;line-height:19px}
.tab-foot{left:0;top:864px;width:758px;height:1px;background:var(--line)}

/* newsletter */
.deco{left:520px;top:913px;width:238px;height:183px;background:linear-gradient(200deg,#eef0e2 0%,#fbf4ee 45%,#ffffff 80%)}
.card{left:103px;top:960px;width:553px;height:200px;background:var(--white);box-shadow:0 0 8px rgba(0,0,0,.08)}
.news-title{left:148px;top:1004px;font-size:24px;font-weight:400;white-space:nowrap}
.news-sub{left:148px;top:1037px;width:242px;text-align:center;font-size:7px;color:var(--muted)}
.email{left:149px;top:1092px;width:238px;height:21px;border-bottom:1px solid #bbb;font-size:9px;color:var(--muted);text-align:center}
.email-arrow{left:377px;top:1097px}
.book-art{left:483px;top:1009px;width:127px;height:98px;background:linear-gradient(135deg,#2fa2a8,#1e7f86 60%,#e0b84a);border-radius:2px}
</style>
</head>
<body>

<header class="nav">
  <a style="left:100px">Home</a>
  <a style="left:146px">About</a>
  <a class="active" style="left:195px">Storefront</a>
  <div class="brand"><div class="brand-name">MARGOT</div><div class="brand-tag">AUTHOR &amp; WRITER</div></div>
  <a style="left:465px">Coming Soon</a>
  <a style="left:549px">Featured</a>
  <a style="left:614px">Contact</a>
</header>

<section class="abs banner" role="img" aria-label="Faded photo of a café storefront with shelves"></section>
<h1 class="abs banner-title">Storefront</h1>
<div class="abs crumbs">Home / <span>Storefront</span></div>

<div class="abs product-art" role="img" aria-label="Front and back covers of the children's science book"></div>
<div class="abs price"><s>$30.00</s><b>$25.00</b></div>
<h2 class="abs product-title">Let’s Learn About Science</h2>
<div class="abs rating">
  <svg width="58" height="8" viewBox="0 0 58 8" fill="#e0533c">
    <g id="star"><polygon points="4,0 5,2.8 8,3 5.6,4.8 6.5,8 4,6.2 1.5,8 2.4,4.8 0,3 3,2.8"/></g>
    <use href="#star" x="12"/><use href="#star" x="24"/><use href="#star" x="36"/><use href="#star" x="48"/>
  </svg>
  <em>(5costumer reviews)</em>
</div>
<p class="abs summary">Lorem ipsum dolor sit amet, consectetur cing elit. Suspe ndisse suscipit sagittis leo sit mural estibulum issim alem Lorem ipsum dolor sit amet, AKON lsicn íoifa lkoix consectetur cing elit limat</p>
<div class="abs qty-label">QUANTITY</div>
<div class="abs qty"><span class="step">–</span><span>1</span><span class="step">+</span></div>
<div class="abs cart-btn">ADD TO CART
  <svg width="7" height="7" viewBox="0 0 10 10" fill="none" stroke="#fff" stroke-width="1.2"><path d="M1 1h2l1.2 5h4.6L10 2.5H3.6"/><circle cx="4.6" cy="8.6" r=".8"/><circle cx="8.4" cy="8.6" r=".8"/></svg>
</div>
<div class="abs rule"></div>
<div class="abs meta" style="top:511px">Authors: <i>Written By - Margot Lindell, Illustrated By - Dana Whitcombe</i></div>
<div class="abs meta" style="top:533px">Category: <i>Kids</i></div>

<section class="abs tabs-area"></section>
<div class="abs tab" style="left:221px">Description</div>
<div class="abs tab inactive" style="left:353px">Reviews &nbsp;- 5</div>
<div class="abs tab-line"></div>
<div class="abs tab-underline"></div>
<p class="abs description">Sustainable everyday carry copper mug adaptogen. Ethical fingerstache small batch mixtape. Gastro-pub seitan flag collector, wayfarers green juice hell of plaid celiac. Pickled typewriter viral cloud bread actually. Fixie subway to authentic enamel pin coloring book. Quiet venison sustainable, aesthet-ic fam crafted paper woke lakeside cornhole adaptogen air plant ramps. Cardigan ethical cold brew fixie journal air plant snackwave drinking vinegar, pork belly man bun health goth aesthetic. Ethical tofu cassette, mustache affogato vinyl messenger bag kettle everyday carry. Late night subway tile tousled glass bulb sartorial trust fund post-ironic chambray, 90's coloring book cold-pressed gastropub vape offal vinyl</p>
<div class="abs tab-foot"></div>

<div class="abs deco" role="img" aria-label="Soft desk scene with notebook and plant"></div>
<section class="abs card"></section>
<h2 class="abs news-title">Join The Newsletter</h2>
<div class="abs news-sub">Subscribe To Get In Touch</div>
<div class="abs email">Enter Your E-mail</div>
<svg class="abs email-arrow" width="10" height="8" viewBox="0 0 10 8" fill="none" stroke="#666" stroke-width="1"><path d="M0 4h9M6 1l3 3-3 3"/></svg>
<div class="abs book-art" role="img" aria-label="Stack of teal books with a featured cover"></div>

</body>
</html>
```